Website design for Puddle Jump Kidscare

I need a website designed for my daycare business, Puddle Jump Kidscare, now that I have a new logo. My former website was ok but simple and I did not have a logo yet. It also was created by me using a template and was entirely pink. I loved the bright, happy feel of it but worried it might not appeal as much to potential clients who have sons. Therefore, I need a site which will appeal to both genders while still keeping the cheerful color scheme of my new logo, which has pinks, blue, green and cream.
Updates

Reason: Hello! I am still trying to download my new logo and am sorry it is taking me so long. Hopefully I will it posted by the end of today (US Eastern Standard Time). Thank you all very much for your patience!

Hello! I have finally managed to upload my new logo for you to use in designing my website. I'm sorry it took so long and greatly appreciate your time and creative efforts! I look forward to seeing what is submitted based on my logo design and its style/colors.

Many thanks!

Reason: As I've been traveling and posted my logo file late, I am extending my deadline. I am now back and can focus on providing more and better feedback. I appreciate your patience and submissions very much!

Reason: I need more time to provide feedback and make decisions.

Industry/Entity Type

Daycare

Colors
0192cd
33a6d7
86cae7
cadf82
fbf289
add136
e34197

```html
<!DOCTYPE html>
<html lang="en">
<head>
<meta charset="utf-8">
<title>Puddle Jump Kidscare</title>
<link href="https://fonts.googleapis.com/css2?family=Source+Sans+3:wght@400;600;700&display=swap" rel="stylesheet">
<style>
:root{
  --green:#8cc63f;
  --green-light:#93cb52;
  --green-foot:#b5d55a;
  --green-dark:#6faa28;
  --pink:#e0306a;
  --pink-soft:#f49ac0;
  --cyan:#6cc4cc;
  --brown:#7a5b3e;
  --text:#6a6a6a;
  --blue-link:#33a6d7;
  --cream:#f5f5f0;
  --white:#fff;
}
*{margin:0;padding:0;box-sizing:border-box}
html,body{width:1024px;height:1200px;overflow:hidden}
body{position:relative;font-family:"Source Sans 3",sans-serif;color:var(--text);background:var(--white)}
.abs{position:absolute}
.header{left:0;top:0;width:1024px;height:117px;background:var(--green)}
.brand-box{left:136px;top:0;width:155px;height:132px;background:var(--white);box-shadow:0 2px 6px rgba(0,0,0,.15);border-radius:0 0 4px 4px;display:flex;flex-direction:column;align-items:center;justify-content:center;gap:6px;z-index:3}
.brand-dot{width:22px;height:22px;border-radius:50%;background:var(--pink)}
.brand-name{color:var(--pink);font-weight:700;font-size:21px;line-height:22px;text-align:center}
.topbar{top:10px;left:440px;height:32px;display:flex;font-size:11px;color:var(--white)}
.topbar .item{display:flex;align-items:center;gap:7px;padding:0 12px;border-left:1px solid rgba(255,255,255,.3)}
.topbar svg{width:15px;height:15px}
.nav{top:58px;left:306px;display:flex}
.nav a{display:flex;flex-direction:column;align-items:center;gap:7px;color:var(--white);font-size:12px;text-decoration:none;opacity:.92;position:relative}
.nav a svg{width:20px;height:20px}
.nav a.active::after{content:"";position:absolute;bottom:-17px;border:8px solid transparent;border-bottom-color:var(--white);border-top:0}
.hero{left:0;top:117px;width:1024px;height:465px;background:linear-gradient(100deg,#e8e2dc 0%,#e7b48a 30%,#d58a4e 50%,#e9dcd0 70%,#f4f1ee 100%)}
.callout{left:584px;top:223px;width:305px;height:180px;background:var(--green-light);border-radius:0 14px 30px 0;border-top-left-radius:26px;padding:32px 20px 0 25px;color:var(--white);font-size:29px;line-height:36px;letter-spacing:-.3px}
.callout b{font-weight:700}
.band{left:0;top:582px;width:1024px;height:418px;background:var(--green)}
.panel{left:129px;top:490px;width:767px;height:510px;background:var(--white);border-radius:6px 6px 0 0;overflow:hidden}
.stripe{display:flex;height:6px}
.stripe span{flex:1}
.feature{top:22px;width:240px;text-align:center}
.feature .photo{width:146px;height:146px;border-radius:50%;margin:0 auto}
.feature h2{font-size:19px;font-weight:700;margin-top:16px;letter-spacing:.3px}
.feature p{font-size:12px;line-height:16px;margin-top:6px}
.about-photo{left:25px;top:327px;width:112px;height:152px;background:linear-gradient(160deg,#d9e6ef,#f0c89a 60%,#8ccae6)}
.section-title{font-size:14px;font-weight:700;color:var(--brown)}
.about-text{left:152px;top:327px;width:330px}
.about-text p{font-size:10.5px;line-height:14.5px;margin-top:12px}
.link{color:var(--blue-link);font-size:8.5px;text-decoration:underline;display:inline-block;margin-top:14px}
.news{left:521px;top:326px;width:230px}
.news-item{display:flex;gap:16px;margin-top:18px}
.news-item:first-of-type{margin-top:13px}
.date{width:48px;height:47px;background:var(--pink-soft);color:var(--white);text-align:center;flex:none}
.date b{display:block;font-size:18px;font-weight:400;padding-top:7px;line-height:20px}
.date small{font-size:7px}
.news-item p{font-size:10.5px;line-height:16px}
.news-item a{color:var(--blue-link);font-size:7px;font-weight:700;text-decoration:none}
.footer{left:0;top:1000px;width:1024px;height:165px;background:var(--cream)}
.foot-brand{left:138px;top:1036px;width:125px;display:flex;flex-direction:column;align-items:center;gap:6px}
.col{top:1030px}
.col h3{font-size:11px;font-weight:600;color:var(--brown);margin-bottom:10px}
.col li{list-style:none;font-size:10px;line-height:19px;letter-spacing:.3px}
.col li::before{content:"›";color:#bbb;margin-right:7px}
.col li.on{color:var(--green-dark)}
.contact li::before{content:none}
.contact li{display:flex;gap:9px;line-height:24px}
.contact svg{width:11px;height:11px;margin-top:6px;flex:none}
.map{left:714px;top:1054px;width:174px;height:81px;background:linear-gradient(135deg,#e6e3dc,#f2efe6 45%,#a9c8e6 55%,#ece8dd)}
.bottom{left:0;top:1165px;width:1024px;height:35px;background:var(--green-foot);color:var(--white);font-size:10px;display:flex;align-items:center;justify-content:space-between;padding:0 139px 0 135px}
</style>
</head>
<body>
<header class="abs header"></header>
<div class="abs brand-box"><span class="brand-dot"></span><span class="brand-name">Puddle Jump<br>Kidscare</span></div>

<div class="abs topbar">
  <div class="item"><svg viewBox="0 0 16 16" fill="none" stroke="#fff" stroke-width="1.5"><circle cx="8" cy="8" r="6"/><path d="M8 4v4l3 2"/></svg>(Mon - Fri) 8:00AM to 6:00PM</div>
  <div class="item"><svg viewBox="0 0 16 16" fill="none" stroke="#fff" stroke-width="1.3"><rect x="2" y="4" width="12" height="8"/><path d="M2 4l6 5 6-5"/></svg>hello@puddlejumpkids.com</div>
  <div class="item"><svg viewBox="0 0 16 16" fill="#fff"><path d="M4 2l3 3-2 2c1 2 2 3 4 4l2-2 3 3-2 2C7 14 2 9 2 4z"/></svg>+(555) 310-4821</div>
</div>

<nav class="abs nav">
  <a class="active" style="width:64px"><svg viewBox="0 0 20 20" fill="#fff"><path d="M10 2l8 8h-3v8h-4v-5H9v5H5v-8H2z"/></svg>Home</a>
  <a style="width:60px"><svg viewBox="0 0 20 20" fill="#fff" opacity=".6"><circle cx="10" cy="7" r="4"/><path d="M3 18c0-4 3-6 7-6s7 2 7 6z"/></svg>About</a>
  <a style="width:75px"><svg viewBox="0 0 20 20" fill="none" stroke="#fff" stroke-width="1.5" opacity=".6"><path d="M2 4h7v13H2zM11 4h7v13h-7z"/></svg>Services</a>
  <a style="width:94px"><svg viewBox="0 0 20 20" fill="none" stroke="#fff" stroke-width="1.6" opacity=".6"><circle cx="10" cy="10" r="8"/><path d="M6 10l3 3 5-6"/></svg>Hours &amp; Fees</a>
  <a style="width:72px"><svg viewBox="0 0 20 20" fill="none" stroke="#fff" stroke-width="1.5" opacity=".6"><rect x="4" y="3" width="12" height="15"/><path d="M7 7h6M7 10h6M7 13h6"/></svg>Policies</a>
  <a style="width:66px"><svg viewBox="0 0 20 20" fill="#fff" opacity=".6"><path d="M2 6h4l2-2h4l2 2h4v11H2z"/><circle cx="10" cy="11" r="3" fill="#8cc63f"/></svg>Photos</a>
  <a style="width:96px"><svg viewBox="0 0 20 20" fill="#fff" opacity=".6"><ellipse cx="11" cy="8" rx="7" ry="5"/><path d="M5 12l-2 5 6-3z"/></svg>Testimonials</a>
  <a style="width:70px"><svg viewBox="0 0 20 20" fill="none" stroke="#fff" stroke-width="1.5" opacity=".6"><rect x="2" y="5" width="16" height="11"/><path d="M2 5l8 6 8-6"/></svg>Contact</a>
</nav>

<div class="abs hero" role="img" aria-label="Photo of three smiling toddlers sitting together among colourful toys"></div>
<div class="abs callout">A playspace where children can <b>play, create, and imagine!</b></div>

<div class="abs band"></div>
<main class="abs panel">
  <div class="stripe"><span style="background:var(--green)"></span><span style="background:var(--pink)"></span><span style="background:var(--cyan)"></span></div>
  <section class="abs feature" style="left:5px">
    <div class="photo" role="img" aria-label="Photo of children building with toy blocks" style="background:linear-gradient(150deg,#e8c9a0,#9bbf6a 60%,#d9643d)"></div>
    <h2 style="color:var(--green-dark)">LEARNING</h2>
    <p>We develop age-appropriate activities that introduce and strengthen academic and to hone their social skills.</p>
  </section>
  <section class="abs feature" style="left:261px">
    <div class="photo" role="img" aria-label="Photo of a child with paint-covered hands" style="background:linear-gradient(150deg,#5a7a3a,#e6b8a0 50%,#7a4ab0)"></div>
    <h2 style="color:var(--pink)">CREATIVITY</h2>
    <p>We offer children a wide range of creative opportunities including art projects, toddler yoga lessons, and a large selection of books and games.</p>
  </section>
  <section class="abs feature" style="left:517px">
    <div class="photo" role="img" aria-label="Photo of a girl and woman sharing a pretend tea party" style="background:linear-gradient(150deg,#b89880,#e6cdb6 55%,#e88aa8)"></div>
    <h2 style="color:var(--cyan)">SHARING</h2>
    <p>We strive to include enrichment activities that extend your child's understanding of the world and their role in it.</p>
  </section>

  <div class="abs about-photo" role="img" aria-label="Photo of children drawing at a classroom table with a teacher"></div>
  <section class="abs about-text">
    <h2 class="section-title">About Puddle Jump Kidscare</h2>
    <p>We are a few blocks from the Line 4 tram and the Maple Avenue bus route, and we offer flexible hourly childcare, making it as easy as possible for busy parents on the go to arrange their children's care.</p>
    <p>We invite you to learn more about us and hope you will visit us soon</p>
    <a class="link">READ MORE</a>
  </section>

  <section class="abs news">
    <h2 class="section-title">Latest News</h2>
    <div class="news-item"><div class="date"><b>05</b><small>May 2014</small></div><p>We are thrilled to have found a new cheerful space with a private backyard... <a>▸READ MORE</a></p></div>
    <div class="news-item"><div class="date"><b>05</b><small>May 2014</small></div><p>We are thrilled to have found a new cheerful space with a private backyard... <a>▸READ MORE</a></p></div>
  </section>
</main>

<footer class="abs footer"></footer>
<div class="abs foot-brand"><span class="brand-dot"></span><span class="brand-name">Puddle Jump<br>Kidscare</span></div>
<div class="abs col" style="left:312px"><h3>Navigation</h3><ul><li class="on">Home</li><li>About</li><li>Services</li><li>Contact</li></ul></div>
<div class="abs col" style="left:438px"><h3>Links</h3><ul><li>Hours &amp; Fees</li><li>Policies</li><li>Testimonials</li><li>Photos</li></ul></div>
<div class="abs col contact" style="left:566px"><h3>Contact Us</h3><ul>
  <li><svg viewBox="0 0 16 16" fill="#bbb"><path d="M4 1l3 3-2 2c1 2 2 3 4 4l2-2 3 3-2 3C7 14 1 9 1 4z"/></svg>+1 555-014-2290</li>
  <li><svg viewBox="0 0 16 16" fill="#ccc"><rect x="1" y="3" width="14" height="10"/></svg>info@puddlejumpkids.com</li>
  <li><svg viewBox="0 0 16 16" fill="#ccc"><path d="M8 1a5 5 0 015 5c0 4-5 9-5 9S3 10 3 6a5 5 0 015-5z"/></svg><span style="line-height:19px;margin-top:2px">Address, Your Country<br>Your Zip Code</span></li>
</ul></div>
<div class="abs col" style="left:715px"><h3>Visit Us</h3></div>
<div class="abs map" role="img" aria-label="Street map showing the daycare location"></div>
<div class="abs bottom"><span>Copyright 2014 © Puddle Jump Kidscare - All Rights Reserved</span><span>Site Map &nbsp; • &nbsp; Privacy Policy</span></div>
</body>
</html>
```